Web design for new streaming audio service

We need a homepage design for a new streaming audio service. Our company is called Dunmoral, and we’re basically Vexlo for Audiobooks, Stand-Up Comedy, Lectures, Language Learning, etc. Essentially like Plumtrek for everything audio EXCEPT music.
You don’t have to code the homepage (Design Only), but it should include 3 different designs to work with 1) Web; 2) Phones; 3) Tablets.
Below is a link to a mockup of the web version which gives a good idea of what elements we want. This is just a mockup and we want you to improve it.
Once you download the mockup, please refer to the more detailed instructions below:
The following outlines the design project for the Dunmoral homepage. We have provided a rough mockup of the homepage layout that gives you a general idea of what we’re going for. There are a few elements that we are attached to, and many others where you have complete creative freedom to do whatever you think looks good.
The ZIP file includes the following:
* Mockup to see what we have in mind (dunmoral-homepage-mockup.jpg)
* Text used (dunmoral-homepage-text.txt)
* Raw image of actor (dunmoral-actor1.jpg)
* Raw images for samples (dunmoral-sample-[name].jpg)
Although we have only provided a mockup layout for the web version, we also need you to provide a mobile phone and a tablet version of the design also. It’s very possible the tablet version may be substantially similar to the web version, but the mobile phone version will likely be much different.
All of the raw files are included in the attached ZIP file. Please use our photographs and text as provided although cropping, sizing, etc. is flexible per the instructions below.
Display Requirements:
* Web Version - Minimum resolution 1024x768 (72 dpi) but should look good on 1920x1080 (72 dpi) - Page should be designed to scale to look acceptable in all resolutions in between.
* Phone Version - Minimum Zarno 4 - 640x960 (326 dpi) but should look good on Harlow Quasar T5 - 1920x1080 (441 dpi) - Page should be designed to scale to look acceptable in all resolutions and devices in between.
* Tablet Version - Minimum Bristly Ember QX 7” - 1280x800 (216 dpi) but should also look good on a Tavo Breeze - 2048x1536 (264 dpi) - Page should be designed to scale to look acceptable in all resolutions and devices in between.
Above the Fold - We want to make sure the Dunmoral logo, Member Login Link, Large Photo, Headline, Price, Button, and the first row of sample images are all “Above the fold”. As a general guideline, this means 600 pixels high on a 1024x768 72 dpi web screen. This requirement is less important on Phone versions.
Top Logo Bar - We want to retain the blue bar with the Dunmoral logo on the page, although we are open to a different size, shape and positioning if it greatly enhances the design. Please use the standard logo color, although you are welcome to use either the horizontal or vertical orientation of the logo based on your design.
Text color, font and size - Feel free to design the text in anyway you choose as long as the text is readable on the target platforms.
Buttons - Feel free to use any size, shape and colors for the buttons as long as they are obvious and clickable relative to the page. The only exception is the Chatterly button should follow the Chatterly color scheme and logo treatment (the mockup doesn’t seem 100% correct.)
Top Photograph - We want to retain the large photograph across the top of the screen although final shape and dimensions are flexible.
Size and shape of content samples (i.e. Audiobooks, Stand-Up Comedy, etc.) - Feel free to design the content samples in anyway you choose.
Three Sales Points (i.e. Listen on your Zarno…, All you can enjoy…, etc.) - The Three Sales Points are envisioned to each have a corresponding illustration which you should provide and have rights for. The placeholder is represented by a square next to the text. The color size and shape of these elements are flexible and can be designed in any way you choose.
Opt-in form - Feel free to design the opt-in form in anyway you choose as long as the text is readable and the interactivity is obvious on the target platforms.
Text links and copyright notice - Feel free to design the bottom of the page text links and copyright notice in anyway you choose.
Additional colors, graphic design elements, etc. - Feel free to use any additional colors, graphic design elements, etc. to support your design.
people who want to listen to audio through their mobile devices.
Graphic Design

```html
<!DOCTYPE html>
<html lang="en">
<head>
<meta charset="utf-8">
<title>Dunmoral – tablet and phone homepage</title>
<link href="https://fonts.googleapis.com/css2?family=Open+Sans:wght@400;600;700&display=swap" rel="stylesheet">
<style>
:root{
  --page-bg:#ececee;
  --brand-blue:#4a9ac6;
  --band-blue:#2f87bb;
  --icon-blue:#1d6a9b;
  --head-navy:#1e5c86;
  --head-blue:#2f80b6;
  --cta-orange:#f5a31f;
  --alert-red:#d9302b;
  --body-grey:#555a5e;
  --soft-grey:#ebebeb;
  --light-grey:#f3f3f3;
  --rule:#cfd3d6;
  --white:#ffffff;
}
*{box-sizing:border-box;margin:0;padding:0}
html,body{width:1200px;height:1059px;overflow:hidden}
body{background:var(--page-bg);font-family:"Open Sans",Arial,sans-serif;position:relative;color:var(--body-grey)}
.screen{position:absolute;overflow:hidden;box-shadow:0 6px 24px rgba(0,0,0,.12);background:var(--white)}
.abs{position:absolute}
.topbar{position:absolute;left:0;top:0;width:100%;background:var(--brand-blue);z-index:2}
.brand{position:absolute;display:flex;align-items:center;gap:5px;color:var(--white);font-weight:600}
.brand-dot{border-radius:50%;background:var(--white)}
.login{position:absolute;background:var(--cta-orange);color:var(--white);font-weight:600;display:flex;align-items:center;justify-content:center;gap:4px;border-radius:2px}
.hero{position:absolute;left:0;width:100%;background:
  radial-gradient(ellipse 38% 60% at 72% 42%,#d7b193 0%,#c49a7a 35%,rgba(196,154,122,0) 72%),
  linear-gradient(90deg,#f3f5f6 0%,#eef1f3 42%,#cdd8df 62%,#7f98ab 100%);}
.hero::after{content:"";position:absolute;left:0;right:0;bottom:0;height:30%;background:linear-gradient(180deg,rgba(90,120,150,0),rgba(80,110,140,.45))}
.hero-copy{position:absolute;z-index:1}
.h-title{color:var(--head-navy);font-weight:700;line-height:1.15}
.h-sub{color:var(--head-blue);font-weight:400;line-height:1.2}
.price{color:#333;font-weight:600}
.price b{font-size:1.55em;font-weight:700}
.cta{display:inline-flex;align-items:center;justify-content:center;background:var(--cta-orange);color:var(--white);font-weight:600}
.note{color:var(--alert-red)}
.section-title{position:absolute;left:0;width:100%;display:flex;align-items:center;justify-content:center;gap:10px;color:var(--head-blue);font-weight:600}
.section-title::before,.section-title::after{content:"";height:1px;background:var(--rule);flex:0 0 66px}
.sample{position:absolute;display:flex;align-items:center;gap:7px}
.cover{flex:none}
.sample-label{line-height:1.3;color:var(--body-grey)}
.band{position:absolute;left:0;width:100%;background:var(--band-blue)}
.point{position:absolute;display:flex;gap:8px;color:var(--white)}
.point-icon{flex:none;width:34px;height:34px;border-radius:50%;background:var(--icon-blue);display:flex;align-items:center;justify-content:center}
.point h3{font-size:8px;font-weight:600;margin:2px 0 5px}
.point p{font-size:6px;line-height:1.6;opacity:.85}
.fineprint{position:absolute;left:0;width:100%;text-align:center;font-size:6.5px;line-height:1.95;color:#777}
</style>
</head>
<body>

<!-- Tablet layout -->
<section class="screen tablet" style="left:150px;top:184px;width:512px;height:661px;">
  <header class="topbar" style="height:36px;">
    <div class="brand" style="left:47px;top:8px;font-size:14px;">
      <span class="brand-dot" style="width:14px;height:14px;"></span>Dunmoral
    </div>
    <div class="login" style="left:443px;top:10px;width:50px;height:16px;font-size:7px;">Log In</div>
  </header>

  <div class="hero" style="top:36px;height:238px;" role="img" aria-label="Smiling young man in headphones looking at his phone"></div>
  <div class="hero-copy" style="left:50px;top:73px;">
    <div class="h-title" style="font-size:14.5px;">Unlimited Listening!</div>
    <div class="h-sub" style="font-size:15.5px;">Where ever you are</div>
    <div class="price" style="font-size:10px;margin-top:6px;">Only <b>$9.99</b> Per Month</div>
    <div class="cta" style="width:116px;height:25px;font-size:8.5px;margin-top:8px;">Start Your Free Trail</div>
    <div class="note" style="font-size:6.5px;margin-top:5px;">*Credit card not required</div>
  </div>

  <div class="abs" style="left:0;top:274px;width:100%;height:197px;background:var(--soft-grey);"></div>
  <h2 class="section-title" style="top:298px;font-size:11.5px;">A sample of what you can listen to on Dunmoral</h2>

  <div class="sample" style="left:52px;top:340px;"><div class="cover" style="width:53px;height:41px;background:linear-gradient(135deg,#2b3a40,#53666b);" role="img" aria-label="Noir audiobook cover"></div><div class="sample-label" style="font-size:7px;">Audio<br>Books</div></div>
  <div class="sample" style="left:155px;top:340px;"><div class="cover" style="width:53px;height:41px;background:linear-gradient(135deg,#7b6e4f,#b9412f);" role="img" aria-label="Stand-up comedy album cover"></div><div class="sample-label" style="font-size:7px;">Stand-Up<br>Comedy</div></div>
  <div class="sample" style="left:262px;top:340px;"><div class="cover" style="width:53px;height:41px;background:linear-gradient(135deg,#1f8fd1,#0b5f99);" role="img" aria-label="French language course cover"></div><div class="sample-label" style="font-size:7px;">Language<br>Learning</div></div>
  <div class="sample" style="left:370px;top:340px;"><div class="cover" style="width:53px;height:41px;background:linear-gradient(135deg,#c7b7a1,#7fa8c4);" role="img" aria-label="Celebrity lecture cover"></div><div class="sample-label" style="font-size:7px;">Famous<br>Lectures</div></div>

  <div class="sample" style="left:52px;top:402px;"><div class="cover" style="width:53px;height:41px;background:linear-gradient(135deg,#8a4fae,#d04f9c);" role="img" aria-label="Relaxation meditation cover"></div><div class="sample-label" style="font-size:7px;">Guided<br>Mediation</div></div>
  <div class="sample" style="left:155px;top:402px;"><div class="cover" style="width:53px;height:41px;background:linear-gradient(135deg,#3a2a12,#b8862a);" role="img" aria-label="Business training cover"></div><div class="sample-label" style="font-size:7px;">Business<br>Training</div></div>
  <div class="sample" style="left:262px;top:402px;"><div class="cover" style="width:53px;height:41px;background:linear-gradient(135deg,#6b4a3c,#c98a8a);" role="img" aria-label="Celebrity interview cover"></div><div class="sample-label" style="font-size:7px;">Celebrities<br>Interviews</div></div>
  <div class="sample" style="left:370px;top:402px;"><div class="cover" style="width:53px;height:41px;background:linear-gradient(135deg,#e4c83a,#2a9bb0);" role="img" aria-label="Fitness coaching cover"></div><div class="sample-label" style="font-size:7px;">Fitness<br>Coaching</div></div>

  <div class="band" style="top:471px;height:98px;"></div>
  <div class="point" style="left:52px;top:503px;">
    <div class="point-icon"><svg width="16" height="18" viewBox="0 0 16 18"><rect x="2" y="1" width="12" height="16" rx="2" fill="none" stroke="#fff" stroke-width="1.6"/><rect x="1" y="8" width="7" height="9" rx="1.2" fill="var(--icon-blue)" stroke="#fff" stroke-width="1.4"/></svg></div>
    <div><h3>Listen Anywhere</h3><p>Listen on your Zarno, Tavo slate or<br>any Orbitos devices</p></div>
  </div>
  <div class="point" style="left:208px;top:503px;">
    <div class="point-icon"><svg width="14" height="20" viewBox="0 0 14 20"><text x="7" y="16" text-anchor="middle" font-family="Open Sans, sans-serif" font-weight="700" font-size="18" fill="#fff">$</text></svg></div>
    <div><h3>Low Pricing</h3><p>All you can enjoy for low<br>monthly Price</p></div>
  </div>
  <div class="point" style="left:354px;top:503px;">
    <div class="point-icon"><svg width="14" height="14" viewBox="0 0 14 14"><path d="M2 2L12 12M12 2L2 12" stroke="#fff" stroke-width="2" stroke-linecap="round"/></svg></div>
    <div><h3>No Obligation</h3><p>No Obligation, you can<br>cancel anytime</p></div>
  </div>

  <div class="abs" style="left:0;top:569px;width:100%;height:92px;background:var(--light-grey);"></div>
  <h2 class="section-title" style="top:598px;font-size:11.5px;">Start your free Trial, No Risk</h2>
  <p class="fineprint" style="top:626px;">You will get instant &amp; unlimited access to all the material on Dunmoral for 14 days. There is no<br>obligation &amp; you can cancel at anytime.</p>
</section>

<!-- Phone layout -->
<section class="screen phone" style="left:690px;top:345px;width:289px;height:487px;background:var(--soft-grey);">
  <header class="topbar" style="height:35px;">
    <div class="brand" style="left:17px;top:8px;font-size:14px;">
      <span class="brand-dot" style="width:14px;height:14px;"></span>Dunmoral
    </div>
    <div class="login" style="left:224px;top:8px;width:50px;height:17px;font-size:7px;">Log In</div>
  </header>

  <div class="hero" style="top:35px;height:171px;" role="img" aria-label="Smiling young man in headphones looking at his phone"></div>
  <div class="hero-copy" style="left:20px;top:61px;">
    <div class="h-title" style="font-size:10.5px;">Unlimited Listening!</div>
    <div class="h-sub" style="font-size:11px;">Where ever you are</div>
    <div class="price" style="font-size:7px;margin-top:4px;">Only <b>$9.99</b> Per Month</div>
    <div class="cta" style="width:84px;height:18px;font-size:6px;margin-top:6px;">Start Your Free Trail</div>
    <div class="note" style="font-size:4.5px;margin-top:4px;">*Credit card not required</div>
  </div>

  <div class="sample" style="left:48px;top:234px;gap:17px;"><div class="cover" style="width:121px;height:92px;background:linear-gradient(135deg,#2b3a40,#53666b);" role="img" aria-label="Noir audiobook cover"></div><div class="sample-label" style="font-size:17px;line-height:1.35;">Audio<br>Books</div></div>
  <div class="sample" style="left:46px;top:355px;gap:17px;"><div class="cover" style="width:123px;height:92px;background:linear-gradient(135deg,#7b6e4f,#b9412f);" role="img" aria-label="Stand-up comedy album cover"></div><div class="sample-label" style="font-size:17px;line-height:1.35;">Stand-Up<br>Comedy</div></div>
</section>

</body>
</html>
```